Bookcover: Ways to Turn Into a Bold Pathfinder

I am publishing a super-low-cost innovation book for €4,99 on Quillmere Open Press to help everyone become a great innovator: young ambitious people without college education nor a big budget. Do you want to help me?

Brief:
Design a book cover 1600 x 2560 pixels for QOP.
Main title: Ways to Turn Into a Bold Pathfinder
Sub title: mindset - insights - skills & tools
Author: Joost ter Brakel
Design: captive, and appealing to everyone
Target Group: young ambitious people without college education

For quillmere please format the height/width ratio of 1.6:1

```html
<!DOCTYPE html>
<html lang="en">
<head>
<meta charset="utf-8">
<title>Ways to Turn Into a Bold Pathfinder — Book Cover</title>
<link rel="stylesheet" href="https://fonts.googleapis.com/css2?family=Bebas+Neue&family=Roboto:wght@500&display=swap">
<style>
  :root {
    --page: #ffffff;
    --cover-blue: #404b8e;
    --band-yellow: #f8d673;
    --title-white: #ffffff;
    --bulb-yellow: #e9c23a;
    --bulb-grey: #8f8f8f;
  }
  html, body {
    margin: 0;
    padding: 0;
    width: 1200px;
    height: 1200px;
    overflow: hidden;
    background: var(--page);
  }
  .canvas {
    position: relative;
    width: 1200px;
    height: 1200px;
  }
  .book-cover {
    position: absolute;
    left: 0;
    top: 0;
  }
  .title-line {
    font-family: "Bebas Neue", Impact, sans-serif;
    fill: var(--title-white);
  }
  .title-highlight {
    font-family: "Bebas Neue", Impact, sans-serif;
    fill: var(--cover-blue);
  }
  .subtitle {
    font-family: "Roboto", Arial, sans-serif;
    font-weight: 500;
    fill: var(--title-white);
  }
  .author {
    font-family: "Bebas Neue", Impact, sans-serif;
    fill: var(--title-white);
  }
  .author-surname { fill: var(--band-yellow); }
  .cover-bg { fill: var(--cover-blue); }
  .torn-band { fill: var(--band-yellow); }
  .torn-edge { fill: none; stroke: var(--title-white); stroke-width: 3; stroke-linejoin: round; }
</style>
</head>
<body>
<div class="canvas">
  <svg class="book-cover" width="1200" height="1200" viewBox="0 0 1200 1200" xmlns="http://www.w3.org/2000/svg">
    <defs>
      <linearGradient id="bulbTone" x1="0" y1="0" x2="0" y2="1">
        <stop offset="0" stop-color="#f0cc45"/>
        <stop offset="0.7" stop-color="#d9b43a"/>
        <stop offset="1" stop-color="#9a9a9a"/>
      </linearGradient>
    </defs>

    <rect class="cover-bg" x="293" y="140" width="614" height="920"/>

    <text class="title-line" x="326" y="283" font-size="157" textLength="348" lengthAdjust="spacingAndGlyphs">WAYS TO</text>
    <text class="title-line" x="326" y="396" font-size="155" textLength="465" lengthAdjust="spacingAndGlyphs">TURN INTO A</text>
    <text class="title-line" x="326" y="557" font-size="210" textLength="355" lengthAdjust="spacingAndGlyphs">BOLD</text>

    <rect class="idea-bulb" x="700" y="415" width="136" height="152" rx="10" fill="url(#bulbTone)"
          role="img" aria-label="Photo of a light bulb made of crumpled yellow paper with light rays"/>

    <path class="torn-band" d="M293 584 L318 580 L345 584 L380 581 L420 583 L452 579 L490 584 L530 582 L560 578 L600 583 L640 580 L680 584 L720 580 L760 583 L800 579 L840 584 L875 580 L907 582 L907 750 L880 748 L850 752 L815 748 L780 752 L745 749 L710 753 L670 748 L635 751 L600 747 L560 752 L525 749 L490 753 L450 748 L410 751 L375 747 L345 750 L330 743 L315 746 L293 750 Z"/>
    <path class="torn-edge" d="M293 584 L318 580 L345 584 L380 581 L420 583 L452 579 L490 584 L530 582 L560 578 L600 583 L640 580 L680 584 L720 580 L760 583 L800 579 L840 584 L875 580 L907 582"/>
    <path class="torn-edge" d="M907 750 L880 748 L850 752 L815 748 L780 752 L745 749 L710 753 L670 748 L635 751 L600 747 L560 752 L525 749 L490 753 L450 748 L410 751 L375 747 L345 750 L330 743 L315 746 L293 750"/>

    <text class="title-highlight" x="327" y="727" font-size="164" textLength="540" lengthAdjust="spacingAndGlyphs">PATHFINDER</text>

    <text class="subtitle" x="326" y="838" font-size="51" textLength="543" lengthAdjust="spacingAndGlyphs">MINDSET - INSIGHTS -</text>
    <text class="subtitle" x="326" y="892" font-size="51" textLength="392" lengthAdjust="spacingAndGlyphs">SKILLS &amp; TOOLS</text>

    <text class="author" x="327" y="1009" font-size="69" textLength="370" lengthAdjust="spacingAndGlyphs">JOOST TER <tspan class="author-surname">BRAKEL</tspan></text>
  </svg>
</div>
</body>
</html>
```